MBRDC redesign and update stationary bc envelopes.

Stationary, Envelopes, Brochures, Business Card. Need to add second surgeon and two other offices. I need everything to match. I am a oral & maxillofacial surgeon.
Additional surgeon and three office addresses.
Jae Min Park, DMD, MD, INC

3718 Silver Meadow Parkway
El Dorado Hills, CA 95762

642 Lorin Way, Suite 101
Folsom, CA. 95630

2317 Vale Street, Suite 105
Auburn, CA. 95603
Updates

Logo design uploaded. Zapfino Extra/Adobe Garamond/Palatino are fonts used before. Not sure what is on exisiting stationary.

Target Market(s)

Referral dentist and sometimes patients. I am a oral & Maxillofacial surgeon.

Industry/Entity Type

Dental Clinic

Font styles to use
Serif
Script

Requirements
Must have
• Color of existing stationary. Update is possible.
Nice to have
• Conservative/modern
Should not have
• Playful

```html
<!DOCTYPE html>
<html lang="en">
<head>
<meta charset="utf-8">
<title>MBRDC Stationery Set</title>
<link href="https://fonts.googleapis.com/css2?family=EB+Garamond:wght@400&family=Arimo:wght@400&family=Open+Sans:wght@400;600&display=swap" rel="stylesheet">
<style>
:root{
  --bg:#e4e4e4;
  --paper:#ffffff;
  --brown:#6b4f3a;
  --green:#6a9322;
  --green-text:#6b9a1f;
  --green-card:#6c8f23;
  --dot:#dfe48f;
  --ink:#1e1e1e;
  --body:#4a4a4a;
  --label:#8a8a8a;
}
*{margin:0;padding:0;box-sizing:border-box}
html,body{width:1200px;height:769px;overflow:hidden;background:var(--bg)}
body{position:relative;font-family:"Arimo",Arial,sans-serif;color:var(--ink)}
.piece{position:absolute;background:var(--paper);box-shadow:0 2px 6px rgba(0,0,0,.25);overflow:hidden}
.abs{position:absolute;white-space:nowrap}
.edge{position:absolute;left:0;top:0}
.serif{font-family:"EB Garamond",Georgia,serif}
.doctor{font-family:"EB Garamond",Georgia,serif;color:var(--green-text)}
.brand{font-family:"EB Garamond",Georgia,serif;color:var(--green-text);display:flex;align-items:center;gap:5px}
.brand .mark{border-radius:50%;background:var(--green-text)}
.services{color:var(--green-text);text-align:center}
.services i{display:inline-block;border-radius:50%;background:var(--dot);vertical-align:middle;margin:0 3px}
.rule{position:absolute;height:1px;background:var(--brown)}
.icon{display:inline-block;vertical-align:middle;margin-right:2px}
.sheet-label{position:absolute;left:815px;top:124px;font:400 18px "Arimo",Arial,sans-serif;color:var(--label)}

/* letterhead */
.letterhead{left:86px;top:99px;width:437px;height:560px}
.letterhead .contact{left:267px;top:18px;font-size:6.2px;line-height:8.2px}
.letterhead .contact .doctor{font-size:8px;line-height:10px}
.letterhead .divider{position:absolute;left:257px;top:19px;width:1px;height:68px;background:var(--brown)}
.letter{position:absolute;left:42px;top:102px;width:354px;font-family:"Open Sans",Arial,sans-serif;font-size:7.2px;color:var(--body)}
.letter p{line-height:12.6px;margin-bottom:12.6px;text-align:justify}
.letter .meta{line-height:8.2px;margin-bottom:0}
.signature{width:100px;height:12px;background:linear-gradient(90deg,rgba(74,74,74,.25),rgba(74,74,74,.05))}
.letterhead .footer-address{left:0;width:437px;text-align:center;font-size:7.6px;line-height:11px}
.letterhead .services{left:0;width:437px;font-size:7.8px;line-height:10px}

/* envelope */
.envelope{left:596px;top:171px;width:507px;height:228px}
.envelope .contact{left:101px;top:17px;font-size:6.4px;line-height:8.4px}
.envelope .contact .doctor{font-size:8px;line-height:10px}
.envelope .services{left:0;width:507px;font-size:6.3px;line-height:8.6px}
.envelope .web{left:0;width:507px;text-align:center;font-size:9.5px;letter-spacing:1.6px;color:var(--brown)}

/* business cards */
.card-front{left:606px;top:487px;width:233px;height:137px}
.card-front .contact{left:11px;top:45px;font-size:5.6px;line-height:7.2px}
.card-front .contact .doctor{font-size:8px;line-height:9px}
.card-back{left:861px;top:487px;width:233px;height:137px;background:var(--green-card);color:#fff}
.card-back ul{position:absolute;left:10px;top:71px;list-style:none;font-family:"Open Sans",Arial,sans-serif;font-size:5.6px;line-height:8.5px}
.card-back li::before{content:"";display:inline-block;width:3px;height:3px;border-radius:50%;background:#fff;margin-right:3px;vertical-align:middle}
.card-back .offices{position:absolute;right:9px;top:78px;text-align:right;font-family:"Open Sans",Arial,sans-serif;font-size:5.6px;line-height:8.6px}
.card-back .offices div{margin-bottom:1.3px}
</style>
</head>
<body>

<div class="sheet-label">Envelope</div>

<!-- Letterhead -->
<section class="piece letterhead">
  <svg class="edge" width="20" height="560" viewBox="0 0 20 560" aria-hidden="true">
    <rect x="0" y="0" width="8" height="560" fill="#6b4f3a"/>
    <polygon points="0,454 18,468 18,560 0,560" fill="#6a9322"/>
  </svg>

  <div class="abs brand" style="left:48px;top:42px;font-size:22px">
    <span class="mark" style="width:12px;height:12px"></span>MBRDC
  </div>

  <div class="divider"></div>
  <div class="abs contact">
    <div class="doctor">Robert K. Hallam,DDS,Inc.</div>
    <div>Diplomate of the American Board of</div>
    <div>Oral &amp; Maxillofacial Surgery</div>
    <div class="doctor" style="margin-top:2px">Jae Min Park, DMD, MD, INC</div>
    <div>Dental Implant and Oral Surgery</div>
    <div style="margin-top:3px">
      <svg class="icon" width="6" height="6" viewBox="0 0 10 10"><path d="M2 1l2 2-1 1.5c.8 1.4 1.8 2.4 3 3L7.5 6l2 2-1.5 1.5C4 9 1 6 .5 2z" fill="#6a9322"/></svg>916.555.0148
      <svg class="icon" width="6" height="6" viewBox="0 0 10 10" style="margin-left:3px"><rect x="2" y="0" width="6" height="3" fill="#6a9322"/><rect x="0" y="3.5" width="10" height="4" fill="#6a9322"/><rect x="2" y="8" width="6" height="2" fill="#6a9322"/></svg>916.555.0172
    </div>
    <div><svg class="icon" width="6" height="5" viewBox="0 0 10 8"><rect width="10" height="8" fill="#6a9322"/><path d="M0 0l5 4 5-4" stroke="#fff" fill="none"/></svg>drhallam@mbrdcoralsurgery.com</div>
    <div><svg class="icon" width="6" height="6" viewBox="0 0 10 10"><circle cx="5" cy="5" r="4.3" fill="none" stroke="#6a9322" stroke-width="1.2"/><path d="M.7 5h8.6M5 .7c-2.5 2.5-2.5 6 0 8.6M5 .7c2.5 2.5 2.5 6 0 8.6" stroke="#6a9322" fill="none" stroke-width=".8"/></svg>www.mbrdcoralsurgery.com</div>
  </div>

  <div class="letter">
    <p class="meta">Issuing Date: May 5, 2018</p>
    <p class="meta" style="margin-top:9px">Name Of Employee Mr. XYZABC<br>Address of Employee<br>Address Line 2 etc..</p>
    <p class="meta" style="margin-top:24px;margin-bottom:17px">Dear Mr.XYZABC</p>
    <p>Lorem Ipsum has been the industry's standard dummy text ever since the 1500s, when an unknown printer took a galley of type and scrambled it to make a type specimen book. It has survived not only five centuries, but also the leap into electronic typesetting, remaining essentially unchanged. It was popularised in the 1960s with the release of Letraset sheets containing Lorem Ipsum passages, and more recently with desktop publishing software like Aldus PageMaker including versions of Lorem Ipsum.</p>
    <p>Lorem Ipsum is simply dummy text of the printing and typesetting industry. Lorem Ipsum has been the industry's standard dummy text ever since the 1500s, when an unknown printer took a galley of type and scrambled it to make a type specimen book.</p>
    <p>It has survived not only five centuries, but also the leap into electronic typesetting, remaining essentially unchanged. It was popularised in the 1960s with the release of Letraset sheets containing Lorem IpsumIpsum passages.</p>
    <p class="meta" style="margin-top:25px">Yours Sincerely</p>
    <div class="signature" role="img" aria-label="Handwritten signature of Marcus Reed" style="margin-top:9px"></div>
    <p class="meta" style="margin-top:9px;font-size:8.6px;font-weight:600;color:#3a3a3a">Marcus Reed</p>
    <p class="meta" style="margin-top:5px">Managing Director</p>
  </div>

  <div class="abs footer-address" style="top:500px">642 Lorin Way, Suite 101 , Folsom, CA. 95630 | 2317 Vale Street, Suite 105, Auburn, CA. 95603<br>3718 Silver Meadow Parkway, El Dorado Hills, CA 95762</div>
  <div class="rule" style="left:49px;top:524px;width:340px"></div>
  <div class="abs services" style="top:527px">Dentoalveolar Surgery<i style="width:4px;height:4px"></i>Dental Implant Surgery<i style="width:4px;height:4px"></i>Orthognathic Surgery<i style="width:4px;height:4px"></i>Facial Trauma Surgery<br>Preprosthetic and Reconstructive Surgery<i style="width:4px;height:4px"></i>TMJ Disorders and Surgery<i style="width:4px;height:4px"></i>Obstructive Sleep Apnea Surgery</div>
</section>

<!-- Envelope -->
<section class="piece envelope">
  <svg class="edge" width="12" height="228" viewBox="0 0 12 228" aria-hidden="true">
    <rect x="0" y="0" width="6" height="228" fill="#6b4f3a"/>
    <polygon points="0,172 10,182 10,228 0,228" fill="#6a9322"/>
  </svg>

  <div class="abs brand" style="left:18px;top:56px;font-size:17px">
    <span class="mark" style="width:9px;height:9px"></span>MBRDC
  </div>

  <div class="abs contact">
    <div class="doctor">Robert K. Hallam,DDS,Inc.</div>
    <div>Diplomate of the American Board of</div>
    <div>Oral &amp; Maxillofacial Surgery</div>
    <div class="doctor" style="margin-top:2px">Jae Min Park, DMD, MD, INC</div>
    <div>Dental Implant and Oral Surgery</div>
    <div style="margin-top:3px"><svg class="icon" width="4" height="6" viewBox="0 0 8 12"><path d="M4 0a4 4 0 0 1 4 4c0 3-4 8-4 8S0 7 0 4a4 4 0 0 1 4-4z" fill="#6a9322"/><circle cx="4" cy="4" r="1.5" fill="#fff"/></svg>3718 Silver Meadow Parkway, El Dorado Hills, CA 95762</div>
    <div style="margin-top:2px"><svg class="icon" width="4" height="6" viewBox="0 0 8 12"><path d="M4 0a4 4 0 0 1 4 4c0 3-4 8-4 8S0 7 0 4a4 4 0 0 1 4-4z" fill="#6a9322"/><circle cx="4" cy="4" r="1.5" fill="#fff"/></svg>642 Lorin Way, Suite 101 , Folsom, CA. 95630</div>
    <div style="margin-top:2px"><svg class="icon" width="4" height="6" viewBox="0 0 8 12"><path d="M4 0a4 4 0 0 1 4 4c0 3-4 8-4 8S0 7 0 4a4 4 0 0 1 4-4z" fill="#6a9322"/><circle cx="4" cy="4" r="1.5" fill="#fff"/></svg>2317 Vale Street, Suite 105, Auburn, CA. 95603</div>
  </div>

  <div class="abs services" style="top:184px">Dentoalveolar Surgery<i style="width:3px;height:3px"></i>Dental Implant Surgery<i style="width:3px;height:3px"></i>Orthognathic Surgery<i style="width:3px;height:3px"></i>Facial Trauma Surgery<i style="width:3px;height:3px"></i>Preprosthetic and Reconstructive Surgery<br>TMJ Disorders and Surgery<i style="width:3px;height:3px"></i>Obstructive Sleep Apnea Surgery</div>
  <div class="rule" style="left:45px;top:197px;width:112px"></div>
  <div class="rule" style="left:350px;top:197px;width:113px"></div>
  <div class="abs web serif" style="top:203px">www.mbrdcoralsurgery.com</div>
</section>

<!-- Business card front -->
<section class="piece card-front">
  <svg class="edge" width="8" height="137" viewBox="0 0 8 137" aria-hidden="true">
    <rect x="0" y="0" width="4" height="137" fill="#6b4f3a"/>
    <polygon points="0,95 6,101 6,137 0,137" fill="#6a9322"/>
  </svg>

  <div class="abs brand" style="left:134px;top:34px;font-size:16px">
    <span class="mark" style="width:8px;height:8px"></span>MBRDC
  </div>

  <div class="abs contact">
    <div class="doctor">Robert K. Hallam,DDS,Inc.</div>
    <div>Diplomate of the American Board of</div>
    <div>Oral &amp; Maxillofacial Surgery</div>
    <div class="doctor" style="margin-top:4px">Jae Min Park, DMD, MD, INC</div>
    <div>Dental Implant and Oral Surgery</div>
    <div style="margin-top:4px"><svg class="icon" width="5" height="5" viewBox="0 0 10 10"><path d="M2 1l2 2-1 1.5c.8 1.4 1.8 2.4 3 3L7.5 6l2 2-1.5 1.5C4 9 1 6 .5 2z" fill="#6a9322"/></svg>916.555.0148</div>
    <div><svg class="icon" width="5" height="5" viewBox="0 0 10 10"><rect x="2" y="0" width="6" height="3" fill="#6a9322"/><rect x="0" y="3.5" width="10" height="4" fill="#6a9322"/><rect x="2" y="8" width="6" height="2" fill="#6a9322"/></svg>916.555.0172</div>
  </div>
  <div class="abs" style="right:9px;top:109px;font-size:5.8px;font-style:italic">drhallam@mbrdcoralsurgery.com</div>
  <div class="rule" style="left:11px;top:119px;width:213px"></div>
  <div class="abs serif" style="left:0;width:233px;top:122px;text-align:center;font-size:6.6px;letter-spacing:1px;color:var(--green-text)">www.mbrdcoralsurgery.com</div>
</section>

<!-- Business card back -->
<section class="piece card-back">
  <div class="abs" style="left:16px;top:20px;display:flex;align-items:center;gap:6px;font-family:'EB Garamond',Georgia,serif;font-size:24px;color:#fff">
    <span style="width:11px;height:11px;border-radius:50%;background:#fff"></span>MBRDC
  </div>
  <ul>
    <li>Dentoalveolar Surgery</li>
    <li>Dental Implant Surgery</li>
    <li>Orthognathic Surgery</li>
    <li>Facial Trauma Surgery</li>
    <li>Preprosthetic and Reconstructive Surgery</li>
    <li>TMJ Disorders and Surgery</li>
    <li>Obstructive Sleep Apnea Surgery</li>
  </ul>
  <div class="offices">
    <div>3718 Silver Meadow Parkway <svg class="icon" width="4" height="6" viewBox="0 0 8 12"><path d="M4 0a4 4 0 0 1 4 4c0 3-4 8-4 8S0 7 0 4a4 4 0 0 1 4-4z" fill="#fff"/><circle cx="4" cy="4" r="1.5" fill="#6c8f23"/></svg><br>El Dorado Hills, CA 95762&nbsp;&nbsp;</div>
    <div>2317 Vale Street, Suite 105 <svg class="icon" width="4" height="6" viewBox="0 0 8 12"><path d="M4 0a4 4 0 0 1 4 4c0 3-4 8-4 8S0 7 0 4a4 4 0 0 1 4-4z" fill="#fff"/><circle cx="4" cy="4" r="1.5" fill="#6c8f23"/></svg><br>Auburn, CA. 95603&nbsp;&nbsp;</div>
    <div>642 Lorin Way, Suite 101 <svg class="icon" width="4" height="6" viewBox="0 0 8 12"><path d="M4 0a4 4 0 0 1 4 4c0 3-4 8-4 8S0 7 0 4a4 4 0 0 1 4-4z" fill="#fff"/><circle cx="4" cy="4" r="1.5" fill="#6c8f23"/></svg><br>Folsom, CA. 95630&nbsp;&nbsp;</div>
  </div>
</section>

</body>
</html>
```